Business Card Design For Office Furniture Clearance Company

Kestrel Office Clearance - our company name pretty much explains what we do, we clear offices for high end clients, mainly plc's and large international companies.

We require a nice looking business card that displays professionalism but without being too serious.

It would be nice to see just a little more than a conventional boring business card, make sure you add some flare.

Industry/Entity Type

Office Furniture

Contact Information for Business Card

CARD 1

Mark Holloway
Director
mark@kestrelofficeclearance.co.uk
m: 07700 153928

t: 01632 960418
www.kestrelofficeclearance.co.uk

Kestrel Office Clearance
Unit K4 B
2-8 Fenwick Lane
Bletchley
Milton Keynes
ZZ9 4QT

free office clearances… you cant get better than that.

CARD 2

Peter Radford
Director
peter@kestrelofficeclearance.co.uk
m: 07700 382615

t: 01632 960418

Kestrel Office Clearance
Unit K4 B
2-8 Fenwick Lane
Bletchley
Milton Keynes
ZZ9 4QT

Font styles to use
Sans Serif

Requirements
Must have
• A white background - as we have a blue logo.
Nice to have
• Nice use of the logo - play around with this and dissect it.

```html
<!DOCTYPE html>
<html lang="en">
<head>
<meta charset="utf-8">
<title>Kestrel Office Clearance – Business Card</title>
<link rel="stylesheet" href="https://fonts.googleapis.com/css2?family=Lato:wght@400;700&display=swap">
<style>
  :root {
    --brand-blue: #0079c1;
    --brand-deep: #00609c;
    --ink: #333a40;
    --paper: #ffffff;
    --backdrop: #e9ebee;
    --rule: #b9bec4;
  }
  * { margin: 0; padding: 0; box-sizing: border-box; }
  html, body { width: 1138px; height: 1200px; overflow: hidden; }
  body {
    background: var(--backdrop);
    font-family: "Lato", sans-serif;
    position: relative;
    color: var(--ink);
  }
  .card {
    position: absolute;
    width: 670px;
    height: 384px;
    border-radius: 14px;
    overflow: hidden;
    box-shadow: 0 6px 18px rgba(0,0,0,0.18);
  }
  .card--front { left: 218px; top: 198px; background: var(--paper); }
  .card--back { left: 216px; top: 617px; height: 381px; background: var(--brand-blue); }

  .brand {
    position: absolute;
    left: 0; top: 102px;
    width: 337px;
    text-align: center;
  }
  .brand__dot {
    width: 148px; height: 148px;
    border-radius: 50%;
    background: var(--brand-blue);
    margin: 0 auto 22px;
  }
  .brand__name {
    font-weight: 700;
    font-size: 24px;
    color: var(--brand-blue);
    white-space: nowrap;
  }
  .divider {
    position: absolute;
    left: 337px; top: 58px;
    width: 1px; height: 276px;
    background: var(--rule);
  }
  .details { position: absolute; left: 369px; top: 78px; }
  .details__name {
    font-weight: 700; font-size: 24px; line-height: 1.1;
    color: var(--brand-blue);
  }
  .details__role { font-size: 15px; line-height: 1.2; }
  .details__address {
    font-size: 15px; line-height: 19.5px;
    margin-top: 24px;
  }
  .contact-list { list-style: none; margin-top: 10px; }
  .contact-list li {
    display: flex; align-items: center;
    font-size: 15px; height: 21.5px;
    white-space: nowrap;
  }
  .contact-list svg { width: 15px; height: 15px; margin-right: 9px; fill: var(--brand-blue); flex: none; }

  .band { position: absolute; left: 0; bottom: 0; width: 100%; height: 24px; }

  .back-name {
    position: absolute; left: 0; right: 0; top: 168px;
    text-align: center;
    font-weight: 700; font-size: 38px;
    color: var(--paper);
  }
  .back-url {
    position: absolute; left: 0; right: 0; bottom: 20px;
    text-align: center;
    font-size: 16px;
    color: var(--paper);
  }
</style>
</head>
<body>
  <section class="card card--front">
    <div class="brand">
      <div class="brand__dot"></div>
      <div class="brand__name">Kestrel Office Clearance</div>
    </div>
    <div class="divider"></div>
    <div class="details">
      <div class="details__name">Mark Holloway</div>
      <div class="details__role">Director</div>
      <div class="details__address">Unit K4 B, 2-8 Fenwick Lane<br>Ashworth, Northbrook<br>ZZ9 4QT</div>
      <ul class="contact-list">
        <li><svg viewBox="0 0 16 16"><path d="M4 0h8a1.5 1.5 0 0 1 1.5 1.5v13A1.5 1.5 0 0 1 12 16H4a1.5 1.5 0 0 1-1.5-1.5v-13A1.5 1.5 0 0 1 4 0zm0.5 2v10.5h7V2zM8 13.3a.9.9 0 1 0 0 1.8.9.9 0 0 0 0-1.8z"/></svg>07700 153928</li>
        <li><svg viewBox="0 0 16 16"><path d="M3.6 0.6l2.3 2.9c.4.5.3 1.1-.1 1.5L4.6 6.1c.9 2 2.6 3.8 4.7 4.9l1.1-1.2c.4-.4 1-.5 1.5-.1l2.9 2.2c.5.4.6 1.1.2 1.6l-1.2 1.5c-.5.6-1.3.9-2 .6C6.2 13.8 2.2 9.8.4 4.2c-.2-.7 0-1.5.6-2L2.1.5c.5-.4 1.1-.3 1.5.1z"/></svg>01632 960418</li>
        <li><svg viewBox="0 0 16 16"><path d="M0 3h16v10H0zm1.5 1.4v7.2l4-3.6zm13 0l-4 3.6 4 3.6zM2.2 4l5.8 5 5.8-5zm4.4 4.9L2.2 12.3h11.6L9.4 8.9 8 10.1z"/></svg>mark@kestrelofficeclearance.co.uk</li>
        <li><svg viewBox="0 0 16 16"><path d="M8 0a8 8 0 1 0 0 16A8 8 0 0 0 8 0zm-.7 1.6v3H4.9c.6-1.6 1.4-2.7 2.4-3zm1.4 0c1 .3 1.8 1.4 2.4 3H8.7zM5.4 1.9c-.5.7-.9 1.6-1.2 2.7H2.4a6.5 6.5 0 0 1 3-2.7zm5.2 0a6.5 6.5 0 0 1 3 2.7h-1.8c-.3-1.1-.7-2-1.2-2.7zM1.8 6h2.1c-.1.6-.1 1.3-.1 2s0 1.4.1 2H1.8a6.5 6.5 0 0 1 0-4zm3.5 0h2v4h-2c-.1-.6-.1-1.3-.1-2s0-1.4.1-2zm3.4 0h2c.1.6.1 1.3.1 2s0 1.4-.1 2h-2zm3.4 0h2.1a6.5 6.5 0 0 1 0 4h-2.1c.1-.6.1-1.3.1-2s0-1.4-.1-2zM2.4 11.4h1.8c.3 1.1.7 2 1.2 2.7a6.5 6.5 0 0 1-3-2.7zm2.5 0h2.4v3c-1-.3-1.8-1.4-2.4-3zm3.8 0h2.4c-.6 1.6-1.4 2.7-2.4 3zm3.1 0h1.8a6.5 6.5 0 0 1-3 2.7c.5-.7.9-1.6 1.2-2.7z"/></svg>www.kestrelofficeclearance.co.uk</li>
      </ul>
    </div>
    <svg class="band" viewBox="0 0 670 24" preserveAspectRatio="none" aria-hidden="true">
      <rect x="0" y="0" width="670" height="24" fill="var(--brand-blue)"/>
      <polygon points="456,0 670,0 670,24 434,24" fill="var(--brand-deep)"/>
      <line x1="457" y1="0" x2="433" y2="24" stroke="#ffffff" stroke-width="2.5"/>
    </svg>
  </section>

  <section class="card card--back">
    <div class="back-name">Kestrel Office Clearance</div>
    <div class="back-url">www.kestrelofficeclearance.co.uk</div>
  </section>
</body>
</html>
```